Business card for medical clinic

I need an upmarket, modern medical/health business card for my clinic

Contact Information for Business Card

name, address, email, qr code

```html
<!DOCTYPE html>
<html lang="en">
<head>
<meta charset="UTF-8">
<title>Verida Care Group — Business Card</title>
<link rel="stylesheet" href="https://fonts.googleapis.com/css2?family=Montserrat:wght@400;500;700&display=swap">
<style>
  :root {
    --page-bg: #e9ebee;
    --card-white: #ffffff;
    --ink: #1d1f24;
    --brand-blue: #1f7fc0;
    --brand-navy: #1c3457;
    --accent-sky: #2aa3dc;
    --back-start: #1b2f52;
    --back-mid: #2b5f88;
    --back-end: #2ba2d8;
    --back-mark: #223a5e;
  }
  * { box-sizing: border-box; margin: 0; padding: 0; }
  html, body {
    width: 1200px; height: 786px; overflow: hidden;
    background: var(--page-bg);
    font-family: "Montserrat", Arial, sans-serif;
  }
  .sheet {
    position: relative; width: 1200px; height: 786px;
    display: flex; align-items: center; justify-content: center; gap: 40px;
  }
  .card {
    width: 540px; height: 309px; position: relative; overflow: hidden;
    box-shadow: 0 10px 28px rgba(20, 30, 50, 0.18);
  }
  .card--front { background: var(--card-white); }
  .card--back {
    background: linear-gradient(120deg, var(--back-start) 0%, var(--back-mid) 55%, var(--back-end) 100%);
    display: flex; align-items: center; justify-content: center;
  }
  .brand {
    display: flex; align-items: center; gap: 12px;
  }
  .brand__dot {
    width: 20px; height: 20px; border-radius: 50%;
    background: var(--brand-blue); flex: none;
  }
  .brand__name {
    font-weight: 500; font-size: 22px; letter-spacing: 0.08em;
    text-transform: uppercase; color: var(--brand-navy); white-space: nowrap;
  }
  .card--front .brand {
    position: absolute; left: 38px; top: 50%; transform: translateY(-50%);
  }
  .card--front .brand__name { font-size: 17px; }
  .card--back .brand__dot { background: var(--back-mark); width: 26px; height: 26px; }
  .card--back .brand__name { color: var(--back-mark); font-size: 26px; }
  .divider {
    position: absolute; left: 282px; top: 58px; bottom: 58px;
    width: 1.5px; background: var(--accent-sky);
  }
  .contact {
    position: absolute; left: 300px; top: 60px; color: var(--ink);
  }
  .contact__name {
    font-weight: 700; font-size: 19px; color: var(--brand-blue); line-height: 1.1;
  }
  .contact__role { font-size: 11.5px; margin-top: 3px; }
  .contact__list { list-style: none; margin-top: 12px; }
  .contact__item {
    display: flex; align-items: center; gap: 9px;
    font-size: 12px; line-height: 1; margin-bottom: 10px;
  }
  .contact__icon { width: 12px; height: 12px; flex: none; color: var(--accent-sky); }
  .contact__address { font-size: 12px; line-height: 1.3; margin-top: 4px; }
</style>
</head>
<body>
<main class="sheet">
  <section class="card card--front" aria-label="Business card front">
    <div class="brand">
      <span class="brand__dot"></span>
      <span class="brand__name">Verida Care Group</span>
    </div>
    <div class="divider"></div>
    <div class="contact">
      <p class="contact__name">Daniel Hart</p>
      <p class="contact__role">Managing Director</p>
      <ul class="contact__list">
        <li class="contact__item">
          <svg class="contact__icon" viewBox="0 0 24 24" aria-hidden="true"><path fill="currentColor" d="M6.6 10.8a15.1 15.1 0 0 0 6.6 6.6l2.2-2.2a1 1 0 0 1 1-.25 11.4 11.4 0 0 0 3.6.57 1 1 0 0 1 1 1V20a1 1 0 0 1-1 1A17 17 0 0 1 3 4a1 1 0 0 1 1-1h3.5a1 1 0 0 1 1 1c0 1.25.2 2.45.57 3.6a1 1 0 0 1-.25 1z"/></svg>
          555.014.2290
        </li>
        <li class="contact__item">
          <svg class="contact__icon" viewBox="0 0 24 24" aria-hidden="true"><path fill="currentColor" d="M2 5h20v14H2z M2 5l10 7 10-7" /><path d="M2 6l10 7 10-7" stroke="#fff" stroke-width="1.6" fill="none"/></svg>
          hello@veridacare.com
        </li>
        <li class="contact__item">
          <svg class="contact__icon" viewBox="0 0 24 24" aria-hidden="true"><circle cx="12" cy="12" r="10" fill="currentColor"/><path d="M2 12h20M12 2c3 3 3 17 0 20M12 2c-3 3-3 17 0 20" stroke="#fff" stroke-width="1.4" fill="none"/></svg>
          www.veridacare.com
        </li>
      </ul>
      <p class="contact__address">48 Cedar Brook Lane<br>Fairview, TN 37062</p>
    </div>
  </section>

  <section class="card card--back" aria-label="Business card back">
    <div class="brand">
      <span class="brand__dot"></span>
      <span class="brand__name">Verida Care Group</span>
    </div>
  </section>
</main>
</body>
</html>
```